Business Card Design

We like to use greens as you will see in our logo (but not TOO much green). We are a Dental Clinic in a somewhat eccentric community. We do not like the dated sharp designs which we see many dentists use. We're looking for something bright and fresh while still maintaining the integrity of the profession. Elegance is not necessarily what we are going for... we need for the design to be "mature" but also up-lifting.

See our logo.
Updates

Project Deadline Extended
Reason: We have 5 designs which we like. But we'd like to see a few more before committing to a design.

Project Deadline Extended
Reason: We are awaiting revisions to this project. We are still welcoming designs while we wait to see if designers are able to provide to us the revisions we require in order to proceed with a selection.

Target Market(s)

Younger families - ages late 20's to early 40's

Industry/Entity Type

Business

Contact Information for Business Card

Corwel T. Banfry DDS 2730 W. Halvert Rd. Ste. 7 Royal Oak, MI 48391 (248)555-0174 FX (248)555-0189 info@BrightwellDentalCareMi.com BrigthwellDentalCareMi.com on the back of the card we need an appointment reminder (For____ Date___ Time____) with "If you are unable to keep your appointment, kindly give 48 hours notice" at the bottom. No use of teeth in the design. DOUBLE SIDED DESIGN

Requirements
Should not have
• The use of pictures of teeth

```html
<!DOCTYPE html>
<html lang="en">
<head>
<meta charset="utf-8">
<title>Brightwell Dental Care – Business Card</title>
<link rel="stylesheet" href="https://fonts.googleapis.com/css2?family=Open+Sans:ital,wght@0,400;0,600;0,700;1,400&family=Cinzel:wght@500&display=swap">
<style>
  :root {
    --green-dark: #1c6b38;
    --green-mid: #3ca23c;
    --green-lime: #8cc63f;
    --ink: #2b2b2b;
    --rule: #b9b9b9;
    --card: #ffffff;
    --backdrop: #ece7e1;
  }
  * { box-sizing: border-box; margin: 0; padding: 0; }
  html, body { width: 1200px; height: 1178px; overflow: hidden; }
  body {
    background: var(--backdrop);
    font-family: "Open Sans", Arial, sans-serif;
    color: var(--ink);
    position: relative;
  }
  .card {
    position: absolute;
    width: 915px;
    height: 522px;
    background: var(--card);
    border-radius: 26px;
    overflow: hidden;
    box-shadow: 0 2px 6px rgba(0,0,0,.18);
  }
  .card--front { left: 232px; top: 48px; }
  .card--back  { left: 30px;  top: 603px; }

  /* brand name lockup */
  .brand {
    position: absolute;
    display: flex;
    align-items: center;
    gap: 18px;
    color: var(--green-dark);
    font-weight: 600;
  }
  .brand__dot {
    flex: none;
    border-radius: 50%;
    background: var(--green-lime);
  }
  .brand__name { line-height: 1.05; }
  .card--front .brand { left: 56px; top: 150px; font-size: 52px; }
  .card--front .brand__dot { width: 58px; height: 58px; }
  .card--back .brand { right: 40px; top: 40px; font-size: 34px; gap: 12px; }
  .card--back .brand__dot { width: 36px; height: 36px; }
  .brand__line { display: block; }

  /* front: contact column */
  .divider {
    position: absolute;
    left: 478px; top: 48px;
    width: 2px; height: 328px;
    background: var(--rule);
  }
  .contact { position: absolute; left: 501px; top: 52px; }
  .contact__name { font-size: 32px; font-weight: 700; color: var(--green-dark); line-height: 1.2; }
  .contact__title { font-size: 22px; line-height: 1.3; }
  .contact__list { list-style: none; margin-top: 44px; font-size: 21px; }
  .contact__list li { display: flex; align-items: center; gap: 8px; height: 40px; }
  .contact__list svg { width: 20px; height: 20px; fill: var(--ink); flex: none; }
  .contact__address { margin-top: 26px; font-size: 21px; line-height: 1.45; }

  .footer-band { position: absolute; left: 0; bottom: 0; width: 915px; height: 77px; }
  .footer-band svg { position: absolute; inset: 0; }
  .footer-band__url {
    position: absolute; left: 440px; top: 14px;
    font-size: 24px; letter-spacing: 1.6px; color: #fff;
  }

  /* back: appointment reminder */
  .appt__title {
    position: absolute; left: 70px; top: 98px;
    font-family: "Cinzel", Georgia, serif;
    font-size: 35px; font-weight: 500; color: var(--green-dark);
    letter-spacing: .5px;
  }
  .field {
    position: absolute; left: 80px;
    display: flex; align-items: flex-end;
    font-size: 24px; line-height: 1;
  }
  .field__fill {
    border-bottom: 2px dotted #555;
    height: 1px;
    margin: 0 10px 4px;
  }
  .field--name { top: 178px; }
  .field--date { top: 245px; }
  .field--next { top: 310px; align-items: center; }
  .slot {
    width: 164px; height: 36px;
    border: 2px solid #555; border-radius: 5px;
    margin-left: 14px;
  }
  .days {
    position: absolute; left: 0; top: 363px;
    width: 915px; height: 71px;
    display: flex; align-items: center;
    background: linear-gradient(90deg, var(--green-dark) 0 722px, #fff 722px 727px, var(--green-mid) 727px);
    color: #fff; font-size: 24px; font-weight: 600;
    padding-left: 80px;
  }
  .days__item { display: flex; align-items: center; }
  .days__box {
    width: 56px; height: 34px;
    background: #fff; border-radius: 4px;
    margin: 0 22px 0 12px;
  }
  .days__item--sat { margin-left: 12px; }
  .notice {
    position: absolute; left: 0; right: 0; top: 457px;
    text-align: center;
    font-size: 24px; font-style: italic;
  }
</style>
</head>
<body>

<section class="card card--front" aria-label="Business card front">
  <div class="brand">
    <span class="brand__dot"></span>
    <span class="brand__name"><span class="brand__line">Brightwell</span><span class="brand__line">Dental Care</span></span>
  </div>

  <div class="divider"></div>

  <div class="contact">
    <p class="contact__name">Corwel T. Banfry</p>
    <p class="contact__title">DDS</p>
    <ul class="contact__list">
      <li>
        <svg viewBox="0 0 20 20" aria-hidden="true"><circle cx="10" cy="10" r="9" fill="none" stroke="#2b2b2b" stroke-width="1.6"/><path d="M6.5 5.5l2 .2.6 2.4-1.2.9a6 6 0 0 0 3.1 3.1l.9-1.2 2.4.6.2 2a1.5 1.5 0 0 1-1.7 1.2A8 8 0 0 1 5.3 7.2 1.5 1.5 0 0 1 6.5 5.5z"/></svg>
        <span>(248)555-0174</span>
      </li>
      <li>
        <svg viewBox="0 0 20 20" aria-hidden="true"><path d="M5 3h8l2 2v3H5z" fill="none" stroke="#2b2b2b" stroke-width="1.6"/><rect x="1.5" y="8" width="17" height="8" rx="2"/><rect x="5" y="13" width="10" height="5" fill="#fff" stroke="#2b2b2b" stroke-width="1.4"/></svg>
        <span>(248)555-0189</span>
      </li>
      <li>
        <svg viewBox="0 0 20 20" aria-hidden="true"><rect x="1.5" y="4" width="17" height="12" rx="1.5"/><path d="M2.5 5.5l7.5 5.5 7.5-5.5" fill="none" stroke="#fff" stroke-width="1.6"/></svg>
        <span>info@BrightwellDentalCareMi.com</span>
      </li>
    </ul>
    <p class="contact__address">2730 W. Halvert Rd.<br>Ste. 7 Royal Oak, MI 48391</p>
  </div>

  <div class="footer-band">
    <svg viewBox="0 0 915 77" width="915" height="77" aria-hidden="true">
      <polygon points="0,5 428,5 404,31 0,31" fill="var(--green-lime)"/>
      <polygon points="442,0 915,0 915,77 0,77 0,38 410,38" fill="var(--green-dark)"/>
    </svg>
    <span class="footer-band__url">www.brigthwelldentalcaremi.com</span>
  </div>
</section>

<section class="card card--back" aria-label="Appointment reminder card">
  <h2 class="appt__title">YOUR APPOINTMENT</h2>

  <div class="brand">
    <span class="brand__dot"></span>
    <span class="brand__name"><span class="brand__line">Brightwell</span><span class="brand__line">Dental Care</span></span>
  </div>

  <div class="field field--name">
    <span>Name :</span><span class="field__fill" style="width:690px"></span>
  </div>
  <div class="field field--date">
    <span>Date :</span><span class="field__fill" style="width:230px;margin-left:30px"></span>
    <span>Time :</span><span class="field__fill" style="width:246px"></span>
    <span>am / pm</span>
  </div>
  <div class="field field--next">
    <span>Next Appointment</span>
    <span class="slot" style="margin-left:20px"></span>
    <span class="slot"></span>
    <span class="slot"></span>
  </div>

  <div class="days">
    <span class="days__item">MON<span class="days__box"></span></span>
    <span class="days__item">TUE<span class="days__box"></span></span>
    <span class="days__item">WED<span class="days__box"></span></span>
    <span class="days__item">THU<span class="days__box"></span></span>
    <span class="days__item">FRI<span class="days__box"></span></span>
    <span class="days__item days__item--sat">SAT<span class="days__box"></span></span>
  </div>

  <p class="notice">If you are unable to keep your appointment, kindly give 48 hours notice</p>
</section>

</body>
</html>
```